R. Talmont Realty, Inc business card (2 sided), letterhead (1 sided) & #10 envelope (1 sided)

business card of standard size utilizing the attached logo. Side one with logo, Owen Talmont (my name), President / Broker (title), 805-317-2684 (phone), www.rtalmontrealty.example (website), 1726 Harlow Avenue, Suite 4052 San Luis Obiso, CA 93628 (business address) owen.rtalmontrealty@mailbox.example (e-mail address),
Side two - Log

Letterhead and #10 envelope in the same theme
Updates

Project Deadline Extended
Reason: I think a 2 day deadline may be a bit ambitious on my part. I have extended the deadline to 4 days. Thanks!

Industry/Entity Type

Business

```html
<!DOCTYPE html>
<html lang="en">
<head>
<meta charset="utf-8">
<title>R. Talmont Realty, Inc — Business Card</title>
<link rel="stylesheet" href="https://fonts.googleapis.com/css2?family=Noto+Serif:wght@400;700&family=Open+Sans:wght@400;600&display=swap">
<style>
  :root {
    --backdrop: #e9e6e1;
    --card-white: #ffffff;
    --card-dark: #353535;
    --brand-blue: #1d6a9a;
    --ink: #2b2b2b;
    --ink-soft: #3a3a3a;
    --reverse: #f2f2f2;
    --icon-blue: #2a7db0;
  }
  * { box-sizing: border-box; margin: 0; padding: 0; }
  html, body { width: 1200px; height: 1182px; overflow: hidden; }
  body {
    background: var(--backdrop);
    position: relative;
    font-family: "Open Sans", Arial, sans-serif;
  }
  .card {
    position: absolute;
    width: 910px;
    height: 520px;
    box-shadow: 0 2px 8px rgba(0,0,0,0.18);
  }
  .card--front { left: 250px; top: 39px; background: var(--card-white); border: 1px solid #cfcfcf; }
  .card--back { left: 44px; top: 613px; background: var(--card-dark); }

  .wordmark {
    position: absolute;
    display: flex;
    align-items: center;
    gap: 22px;
    font-family: "Noto Serif", Georgia, serif;
    font-weight: 400;
  }
  .wordmark__square { width: 34px; height: 34px; flex: none; }
  .wordmark__name { font-size: 62px; line-height: 1.05; }
  .card--front .wordmark { left: 36px; top: 70px; color: var(--brand-blue); }
  .card--front .wordmark__square { background: var(--brand-blue); }
  .card--back .wordmark { left: 150px; top: 130px; color: var(--reverse); }
  .card--back .wordmark__square { background: var(--reverse); }

  .contact-list { position: absolute; left: 56px; top: 350px; list-style: none; }
  .contact-list__item {
    display: flex; align-items: center; gap: 10px;
    font-size: 22px; color: var(--ink); height: 41px;
  }
  .contact-list__icon { width: 20px; height: 20px; flex: none; }

  .signature { position: absolute; right: 40px; top: 356px; text-align: right; font-family: "Noto Serif", Georgia, serif; }
  .signature__name { font-size: 34px; font-weight: 700; color: var(--brand-blue); line-height: 1.2; }
  .signature__title { font-size: 26px; color: var(--ink-soft); line-height: 1.3; }

  .back-url {
    position: absolute; left: 0; right: 0; top: 428px; text-align: center;
    color: var(--reverse); font-size: 30px; letter-spacing: 3px; font-weight: 600;
  }
</style>
</head>
<body>
  <section class="card card--front" aria-label="Business card, front">
    <div class="wordmark">
      <span class="wordmark__square"></span>
      <span class="wordmark__name">R. Talmont<br>Realty, Inc</span>
    </div>

    <ul class="contact-list">
      <li class="contact-list__item">
        <svg class="contact-list__icon" viewBox="0 0 20 20" aria-hidden="true"><circle cx="10" cy="10" r="9" fill="var(--icon-blue)"/><path d="M7 5.5c-1 1-1 3 1.5 6s5 3.5 6 2.5l-1.8-1.8-1.4.8c-1-.5-2.4-1.9-2.9-2.9l.8-1.4z" fill="#fff"/></svg>
        <span>805-317-2684</span>
      </li>
      <li class="contact-list__item">
        <svg class="contact-list__icon" viewBox="0 0 20 20" aria-hidden="true"><circle cx="10" cy="10" r="9" fill="var(--icon-blue)"/><rect x="5" y="6.5" width="10" height="7" fill="#fff"/><path d="M5 6.5l5 4 5-4" fill="none" stroke="var(--icon-blue)" stroke-width="1.2"/></svg>
        <span>owen.rtalmontrealty@mailbox.example</span>
      </li>
      <li class="contact-list__item">
        <svg class="contact-list__icon" viewBox="0 0 20 20" aria-hidden="true"><circle cx="10" cy="10" r="9" fill="var(--icon-blue)"/><g fill="none" stroke="#fff" stroke-width="1.1"><circle cx="10" cy="10" r="5.5"/><ellipse cx="10" cy="10" rx="2.4" ry="5.5"/><path d="M4.5 10h11"/></g></svg>
        <span>www.rtalmontrealty.example</span>
      </li>
    </ul>

    <div class="signature">
      <p class="signature__name">Owen Talmont</p>
      <p class="signature__title">President / Broker</p>
    </div>
  </section>

  <section class="card card--back" aria-label="Business card, back">
    <div class="wordmark">
      <span class="wordmark__square"></span>
      <span class="wordmark__name">R. Talmont<br>Realty, Inc</span>
    </div>
    <p class="back-url">www.rtalmontrealty.example</p>
  </section>
</body>
</html>
```